Northfield Builders Guild Business card

We are looking for a new business card design with photo included.
Our business is a nonprofit construction contractor membership organization. We offer business education, assist with business setup and licensing, provide safety training, and provide a member directory.
URL: www.builderslinkguild.org
Color code:
CMYK: 0 cyan, 42 magenta, 100 yellow, 0 black for Print.
Hexidecimal: #FF9900
RGB: R 255; G 153; B 0

```html
<!DOCTYPE html>
<html lang="en">
<head>
<meta charset="utf-8">
<title>Northfield Builders Guild – Business Card</title>
<link href="https://fonts.googleapis.com/css2?family=Arimo:wght@400;700&display=swap" rel="stylesheet">
<style>
  :root {
    --bg: #3a3a3a;
    --card: #111111;
    --orange: #ff9900;
    --white: #ffffff;
    --rule: #5a5a5a;
    --font: "Arimo", Arial, sans-serif;
  }
  * { box-sizing: border-box; margin: 0; padding: 0; }
  html, body { width: 1200px; height: 1040px; overflow: hidden; }
  body {
    background: var(--bg);
    font-family: var(--font);
    position: relative;
  }
  .card {
    position: absolute;
    left: 250px;
    width: 700px;
    height: 400px;
    background: var(--card);
    box-shadow: 0 14px 30px rgba(0,0,0,0.55);
    color: var(--white);
  }
  .card--front {
    top: 110px;
    border-radius: 90px 0 90px 0;
  }
  .card--back {
    top: 560px;
    border-radius: 0 90px 0 90px;
  }
  .brand {
    display: flex;
    align-items: center;
    gap: 14px;
    font-weight: 700;
    color: var(--white);
    letter-spacing: 0.5px;
    text-transform: uppercase;
  }
  .brand__dot {
    width: 22px; height: 22px;
    border-radius: 50%;
    background: var(--orange);
    flex: none;
  }
  .card--front .brand {
    position: absolute;
    top: 150px; left: 0; right: 0;
    justify-content: center;
    font-size: 40px;
  }
  .card--front .website {
    position: absolute;
    bottom: 56px; left: 0; right: 0;
    text-align: center;
    font-size: 19px;
    letter-spacing: 0.3px;
  }
  .website__domain { color: var(--orange); }

  .card--back .brand {
    position: absolute;
    left: 40px; top: 150px;
    width: 300px;
    font-size: 30px;
    line-height: 1.1;
  }
  .divider {
    position: absolute;
    left: 370px; top: 70px;
    width: 1px; height: 260px;
    background: var(--rule);
  }
  .contact {
    position: absolute;
    left: 395px; top: 70px;
    right: 20px;
  }
  .contact__name {
    color: var(--orange);
    font-weight: 700;
    font-size: 24px;
    letter-spacing: 0.5px;
  }
  .contact__role {
    font-size: 15px;
    letter-spacing: 0.5px;
    margin-bottom: 12px;
  }
  .contact__list { list-style: none; }
  .contact__item {
    display: flex;
    align-items: center;
    gap: 10px;
    font-size: 18px;
    height: 28px;
  }
  .contact__icon {
    width: 22px; height: 22px;
    border-radius: 50%;
    background: var(--orange);
    display: flex; align-items: center; justify-content: center;
    flex: none;
  }
  .contact__note { color: var(--orange); margin-left: 4px; }
  .contact__address {
    margin-top: 18px;
    font-size: 19px;
    line-height: 1.35;
  }
</style>
</head>
<body>
  <section class="card card--front">
    <div class="brand"><span class="brand__dot"></span>Northfield Builders Guild</div>
    <p class="website">www.<span class="website__domain">builderslinkguild</span>.org</p>
  </section>

  <section class="card card--back">
    <div class="brand"><span class="brand__dot"></span>Northfield Builders Guild</div>
    <div class="divider"></div>
    <div class="contact">
      <p class="contact__name">DANIEL REYES</p>
      <p class="contact__role">MANAGING DIRECTOR</p>
      <ul class="contact__list">
        <li class="contact__item">
          <span class="contact__icon"><svg width="12" height="12" viewBox="0 0 24 24"><path fill="#111" d="M6.6 10.8a15 15 0 0 0 6.6 6.6l2.2-2.2c.3-.3.7-.4 1-.2 1.1.4 2.3.6 3.6.6.6 0 1 .4 1 1V20c0 .6-.4 1-1 1A17 17 0 0 1 3 4c0-.6.4-1 1-1h3.5c.6 0 1 .4 1 1 0 1.3.2 2.5.6 3.6.1.3 0 .7-.2 1z"/></svg></span>
          971) 555-0142<span class="contact__note">(Office)</span>
        </li>
        <li class="contact__item">
          <span class="contact__icon"><svg width="12" height="12" viewBox="0 0 24 24"><rect x="6" y="2" width="12" height="20" rx="2" fill="none" stroke="#111" stroke-width="2.5"/><circle cx="12" cy="18" r="1.3" fill="#111"/></svg></span>
          800-555-0198
        </li>
        <li class="contact__item">
          <span class="contact__icon"><svg width="12" height="12" viewBox="0 0 24 24"><rect x="7" y="2" width="10" height="6" fill="#111"/><rect x="2" y="9" width="20" height="8" rx="2" fill="#111"/><rect x="7" y="15" width="10" height="7" fill="#111" stroke="#ff9900" stroke-width="1.5"/></svg></span>
          503.555.0176
        </li>
        <li class="contact__item">
          <span class="contact__icon"><svg width="12" height="12" viewBox="0 0 24 24"><rect x="2" y="5" width="20" height="14" fill="#111"/><path d="M2 5l10 8 10-8" fill="none" stroke="#ff9900" stroke-width="2"/></svg></span>
          support@nbguild.org
        </li>
      </ul>
      <p class="contact__address">2400 NW Alder Ave<br>Suite #210, Portland, OR 97209</p>
    </div>
  </section>
</body>
</html>
```